Transform Your Giving

I need a tri-fold brochure that will fit in a standard number 10 business envelope. Meadowlark and Allied Services is a charitable nonprofit. The goal of this brochure is to stimulate people into thinking about other ways to make a donation. The design should communicate the essential information on donation options, create a sense of professional integrity, be graphically sharp, easy to read and laid out in a way that doesn't make the material appear crowded.

```html
<!DOCTYPE html>
<html lang="en">
<head>
<meta charset="utf-8">
<title>Transform Your Giving – Meadowlark and Allied Services</title>
<link rel="stylesheet" href="https://fonts.googleapis.com/css2?family=Barlow:wght@300;400;500;600;700;800&display=swap">
<style>
  :root {
    --bg: #757575;
    --navy: #2a2373;
    --navy-deep: #262267;
    --violet: #3b2fb8;
    --green: #41b649;
    --white: #ffffff;
    --ink: #1e1b4b;
  }
  * { box-sizing: border-box; margin: 0; padding: 0; }
  html, body { width: 1096px; height: 1200px; overflow: hidden; background: var(--bg); }
  body { position: relative; font-family: "Barlow", Arial, sans-serif; }

  .brochure { position: absolute; left: 183px; top: 283px; width: 730px; height: 547px; display: flex; }
  .panel { position: relative; width: 243.4px; height: 547px; overflow: hidden; }
  .panel--inside { background: var(--white); }
  .panel--back { background: linear-gradient(180deg, #2c238e 0%, #3a2fc0 40%, #2b238c 65%, var(--navy-deep) 100%); color: var(--white); text-align: center; }
  .panel--cover { background: var(--white); }

  .photo { position: absolute; left: 0; width: 100%; }
  .photo--family { top: 0; height: 240px; background: linear-gradient(160deg, #e9e6e2 0%, #d6c4bc 45%, #8e8580 100%); }
  .photo--couple { top: 92px; height: 220px; background: linear-gradient(180deg, #b9d3ec 0%, #dfe6ee 45%, #cdb9a6 100%); }
  .photo--hands { top: 95px; height: 120px; left: 0; background: radial-gradient(ellipse at 60% 55%, rgba(110,100,230,.55), rgba(60,50,190,0) 70%); }

  .arc { position: absolute; left: 0; width: 100%; }

  .impact { position: absolute; left: 16px; right: 14px; top: 242px; }
  .impact__title { font-weight: 800; font-size: 13.6px; color: var(--navy); letter-spacing: .1px; }
  .impact__text { font-weight: 500; font-size: 11.3px; line-height: 14.2px; color: var(--ink); margin-top: 1px; }

  .options { position: absolute; left: 0; width: 243px; height: 145px; }
  .options text { font-family: "Barlow", Arial, sans-serif; font-weight: 700; font-size: 11.2px; fill: var(--ink); text-anchor: middle; }

  .back__intro { position: absolute; left: 14px; right: 14px; top: 18px; font-size: 9.6px; line-height: 12.2px; font-weight: 500; }
  .back__quote { position: absolute; left: 14px; right: 14px; top: 96px; font-size: 9.4px; line-height: 12.2px; font-weight: 300; }
  .back__will { position: absolute; left: 10px; right: 10px; top: 222px; font-size: 9.4px; line-height: 11.8px; font-weight: 500; }
  .back__will a, .contact__title, .follow__label { color: var(--green); text-decoration: underline; }
  .back__brand { position: absolute; left: 10px; right: 10px; top: 290px; font-size: 14px; line-height: 17px; font-weight: 700; color: var(--white); }

  .contact { position: absolute; left: 10px; right: 10px; top: 355px; }
  .contact__title { font-weight: 700; font-size: 11.4px; }
  .contact__lead { font-size: 9.4px; line-height: 12px; font-weight: 500; margin-top: 2px; }
  .contact__item { font-size: 9.4px; line-height: 12px; font-weight: 300; }
  .contact__icon { display: block; margin: 3px auto 2px; }
  .follow { margin-top: 6px; font-size: 10px; font-weight: 700; display: flex; justify-content: center; align-items: center; gap: 3px; }
  .follow__dot { width: 9px; height: 9px; border-radius: 50%; background: var(--green); display: inline-block; }

  .cover__head { position: absolute; left: 0; right: 0; top: 13px; text-align: center; }
  .cover__title { font-weight: 700; font-size: 19px; line-height: 21px; color: var(--navy); }
  .cover__tag { font-weight: 800; font-size: 19px; line-height: 21px; color: var(--green); }
  .cover__sub { font-weight: 600; font-size: 9.8px; line-height: 12px; color: var(--navy); margin-top: 6px; }
  .cover__brand { position: absolute; left: 0; right: 0; top: 472px; text-align: center; font-weight: 700; font-size: 15px; line-height: 18px; color: var(--navy); }
</style>
</head>
<body>
<svg width="0" height="0" style="position:absolute" aria-hidden="true">
  <defs>
    <g id="badge"><circle r="23" fill="#2a2373"/><circle r="20" fill="none" stroke="#fff" stroke-width="1.2"/></g>
    <g id="glyph-crypto" fill="none" stroke="#fff" stroke-width="3" stroke-linecap="round">
      <path d="M7 -8 A10.5 10.5 0 1 0 7 8"/><path d="M0 -14 V-10 M0 10 V14" stroke-width="2"/>
    </g>
    <g id="glyph-bank" fill="none" stroke="#fff" stroke-width="1.4">
      <path d="M-12 -6 L0 -13 L12 -6 Z"/><circle cx="0" cy="-8.5" r="1.4"/>
      <path d="M-9 -3 V8 M-4.5 -3 V8 M0 -3 V8 M4.5 -3 V8 M9 -3 V8"/><path d="M-12 9 H12 M-13 12 H13"/>
    </g>
    <g id="glyph-gift" fill="none" stroke="#fff" stroke-width="1.4">
      <rect x="-11" y="-5" width="22" height="5"/><rect x="-9" y="0" width="18" height="12"/>
      <path d="M0 -5 V12"/><path d="M0 -5 C-4 -12 -10 -10 -6 -6 Z M0 -5 C4 -12 10 -10 6 -6 Z"/>
    </g>
    <g id="glyph-chart" fill="none" stroke="#fff" stroke-width="1.5">
      <rect x="-11" y="4" width="4" height="6"/><rect x="-4" y="0" width="4" height="10"/><rect x="3" y="-3" width="4" height="13"/>
      <path d="M-12 -1 L-5 -6 L0 -3 L10 -12 M5 -12 H10 V-7"/>
    </g>
    <g id="glyph-annuity" fill="none" stroke="#fff" stroke-width="1.2">
      <rect x="-12" y="-7" width="24" height="18" rx="1.5"/><circle cx="0" cy="-9" r="4" fill="#2a2373"/>
      <path d="M-8 -1 h4 v3 h-4z M-2 -1 h4 v3 h-4z M4 -1 h4 v3 h-4z M-8 5 h4 v3 h-4z M-2 5 h4 v3 h-4z M4 5 h4 v3 h-4z"/>
    </g>
  </defs>
</svg>

<main class="brochure">
  <!-- Inside panel -->
  <section class="panel panel--inside">
    <div class="photo photo--family" role="img" aria-label="Photo of a young woman sharing coffee with a smiling elderly man on a sofa"></div>
    <svg class="arc" style="top:200px" width="243" height="50" viewBox="0 0 243 50" aria-hidden="true">
      <path d="M0 32 Q121 -8 243 32 V50 H0 Z" fill="#fff"/>
      <path d="M0 30 Q121 -10 243 30" fill="none" stroke="#41b649" stroke-width="5"/>
    </svg>
    <div class="impact">
      <h2 class="impact__title">THE IMPACT OF YOUR GIFT</h2>
      <p class="impact__text">Your generosity drives our mission. With every Smart gift you’re supporting Meadowlark and Allied Services. Join our community of Smart Givers today and make an enduring impact. With Smart Giving your generosity reaches further.&nbsp; Begin your Smart Giving journey with us today.</p>
    </div>
    <svg class="options" style="top:390px" viewBox="0 0 243 145" aria-label="Giving options">
      <path d="M71 23 H100 M146 23 H172 M106 90 H139" stroke="#2a2373" stroke-width="1.4" stroke-dasharray="1.5 1.5"/>
      <g transform="translate(48 23)"><use href="#badge"/><use href="#glyph-crypto"/></g>
      <g transform="translate(123 23)"><use href="#badge"/><use href="#glyph-bank"/></g>
      <g transform="translate(195 23)"><use href="#badge"/><use href="#glyph-gift"/></g>
      <g transform="translate(83 90)"><use href="#badge"/><use href="#glyph-chart"/></g>
      <g transform="translate(162 90)"><use href="#badge"/><use href="#glyph-annuity"/></g>
      <text x="48" y="60">CRYPTO</text><text x="123" y="60">DAF’S</text><text x="195" y="60">QCDS</text>
      <text x="83" y="126">STOCKS &amp;</text><text x="83" y="140">SECURITIES</text>
      <text x="162" y="126">CHARITABLE</text><text x="162" y="140">ANNUITY</text>
    </svg>
  </section>

  <!-- Back panel -->
  <section class="panel panel--back">
    <div class="photo photo--hands" role="img" aria-label="Faint photo of two hands reaching toward each other"></div>
    <p class="back__intro">To learn more about Smart Giving Options and how they can benefit you and Meadowlark and Allied Services, please reach out to our team.&nbsp; We’re here to help you navigate these giving methods and answer any question you may have.</p>
    <p class="back__quote">Being kind to others is a way of<br>being good to yourself.<br>Miriam Holloway</p>
    <p class="back__will">If you do not have a will, go to<br><a href="#">www.easywillnow.org</a><br>In 20 minutes you can have a legal will – for free.</p>
    <p class="back__brand">Meadowlark and Allied<br>Services, Inc.</p>
    <div class="contact">
      <h3 class="contact__title">CONTACT US</h3>
      <p class="contact__lead">Have more question? Please contact us at Meadowlark and Allied Services</p>
      <svg class="contact__icon" width="9" height="9" viewBox="0 0 10 10" aria-hidden="true"><circle cx="5" cy="5" r="5" fill="#41b649"/><path d="M5 2.2a1.8 1.8 0 0 1 1.8 1.8C6.8 5.4 5 7.6 5 7.6S3.2 5.4 3.2 4A1.8 1.8 0 0 1 5 2.2z" fill="#fff"/></svg>
      <p class="contact__item">1720 Larkspur Ave.<br>Suite 4 Millbrook, ND&nbsp; 58500</p>
      <svg class="contact__icon" width="9" height="9" viewBox="0 0 10 10" aria-hidden="true"><circle cx="5" cy="5" r="5" fill="#41b649"/><path d="M3 2.5l1.2 1.2-.6.8a4 4 0 0 0 1.9 1.9l.8-.6L7.5 7 6.8 7.7C4.8 7.6 2.4 5.2 2.3 3.2z" fill="#fff"/></svg>
      <p class="contact__item">555-014-2200 (ext. 100)</p>
      <svg class="contact__icon" width="9" height="9" viewBox="0 0 10 10" aria-hidden="true"><circle cx="5" cy="5" r="5" fill="#41b649"/><rect x="2.6" y="3.3" width="4.8" height="3.4" fill="#fff"/><path d="M2.6 3.3L5 5.2 7.4 3.3" stroke="#41b649" stroke-width=".6" fill="none"/></svg>
      <p class="contact__item">jdoyle@meadowlarkallied.org</p>
      <svg class="contact__icon" width="9" height="9" viewBox="0 0 10 10" aria-hidden="true"><circle cx="5" cy="5" r="5" fill="#41b649"/><circle cx="5" cy="5" r="2.6" fill="none" stroke="#fff" stroke-width=".6"/><path d="M2.4 5h5.2M5 2.4c-1.4 1.5-1.4 3.7 0 5.2M5 2.4c1.4 1.5 1.4 3.7 0 5.2" stroke="#fff" stroke-width=".5" fill="none"/></svg>
      <p class="contact__item">www.meadowlarkallied.org</p>
      <p class="follow"><span class="follow__label">FOLLOW US:</span> <span class="follow__dot"></span><span class="follow__dot"></span></p>
    </div>
  </section>

  <!-- Cover panel -->
  <section class="panel panel--cover">
    <header class="cover__head">
      <h1 class="cover__title">Transform Your Giving</h1>
      <p class="cover__tag">Be Strategic, Be Smart</p>
      <p class="cover__sub">Discover the impact of Smart Giving with<br>Meadowlark and Allied Services</p>
    </header>
    <div class="photo photo--couple" role="img" aria-label="Photo of a happy older couple embracing against a bright sky"></div>
    <svg class="arc" style="top:88px" width="244" height="30" viewBox="0 0 244 30" aria-hidden="true">
      <path d="M0 0 H244 V28 Q122 -10 0 28 Z" fill="#fff"/>
      <path d="M0 28 Q122 -10 244 28" fill="none" stroke="#41b649" stroke-width="4"/>
    </svg>
    <svg class="arc" style="top:280px" width="244" height="40" viewBox="0 0 244 40" aria-hidden="true">
      <path d="M0 32 Q122 -8 244 32 V40 H0 Z" fill="#fff"/>
      <path d="M0 30 Q122 -10 244 30" fill="none" stroke="#41b649" stroke-width="4"/>
    </svg>
    <svg class="options" style="top:306px" viewBox="0 0 243 145" aria-label="Giving options">
      <path d="M71 23 H100 M146 23 H172 M106 90 H139" stroke="#2a2373" stroke-width="1.4" stroke-dasharray="1.5 1.5"/>
      <g transform="translate(48 23)"><use href="#badge"/><use href="#glyph-crypto"/></g>
      <g transform="translate(123 23)"><use href="#badge"/><use href="#glyph-bank"/></g>
      <g transform="translate(195 23)"><use href="#badge"/><use href="#glyph-gift"/></g>
      <g transform="translate(83 90)"><use href="#badge"/><use href="#glyph-chart"/></g>
      <g transform="translate(162 90)"><use href="#badge"/><use href="#glyph-annuity"/></g>
      <text x="48" y="60">CRYPTO</text><text x="123" y="60">DAF’S</text><text x="195" y="60">QCDS</text>
      <text x="83" y="126">STOCKS &amp;</text><text x="83" y="140">SECURITIES</text>
      <text x="162" y="126">CHARITABLE</text><text x="162" y="140">ANNUITY</text>
    </svg>
    <p class="cover__brand">Meadowlark and Allied<br>Services, Inc.</p>
  </section>
</main>
</body>
</html>
```